International Dental Education Website

This project is for a small teaching center on endodontic and micro dentistry in Norway. We need a Wordpress website design to display and highlight dental educational courses. Please use our new logo - see attached file. We like lighter, pastel oriented colors. The following sites are nicely laid out and you can use these as a guideline of sorts but I do want a unique site.
http://vorplaxe.example/en, http://www.trelvanmork.example/Education.aspx?currentSection=courses&cid=14,
http://www.quastifel.example/.
Please create a space for a possible video on the home page. Please include a small contact form on the home page(name, email, phone, text box). Would like a horizonatal naviagtion bar. Would like an image to go across the whole top part of the site and this may rotate. Please use a stock image that shows a classroom type setting. Put phone number at the top of the screen. Put address and sitemap in a footer.

Reason: Upcoming vacation with limited internet access. Please continue to submit any designs. Thanks you.

Reason: The client is from a foreign country and is on an extended vacation.

Target Market(s)

General dentists (GPs) and specialists in Endodontics

Industry/Entity Type

Dental

Requirements
Must have
• Sitemap: HOME, COURSES, LECTURER, CONTACT US,
NORWEGIAN/ENGLISH. Phone number is: +47 53169027. Business name and address: Mivo Lark AS, Endodontic Teaching Center,
Tollbeks vei 41C, 0397 Oslo, Norway.

```html
<!DOCTYPE html>
<html lang="en">
<head>
<meta charset="utf-8">
<title>Mivo Lark – Endodontic Teaching Center</title>
<link href="https://fonts.googleapis.com/css2?family=Ubuntu:wght@300;400&family=Open+Sans:wght@400;600;700&display=swap" rel="stylesheet">
<style>
:root{
  --teal:#2f9c9a;
  --teal-dark:#1f6f73;
  --teal-soft:#63c0bd;
  --teal-pale:#e3f4f4;
  --band:#cfecec;
  --ink:#3d3d3d;
  --navy:#0f3d4a;
  --field:#d3ebeb;
  --orange:#e8870c;
  --line:#bfe0e0;
  --white:#ffffff;
}
*{box-sizing:border-box;margin:0;padding:0}
html,body{width:859px;height:1200px;overflow:hidden}
body{position:relative;background:var(--white);font-family:"Open Sans",sans-serif;color:var(--ink)}
.abs{position:absolute}
.top-line{left:0;top:0;width:859px;height:3px;background:var(--teal-soft)}
.hero-band{left:0;top:3px;width:859px;height:408px;background:linear-gradient(#f4fbfb,#e2f4f4)}
.lang-bar{left:456px;top:3px;width:366px;height:35px;background:#e1f3f3;border-radius:0 0 6px 6px;display:flex;align-items:center;padding-left:13px;font-size:10px;color:var(--navy);white-space:nowrap}
.lang-bar .flags{display:flex;gap:5px;margin:0 12px 0 10px}
.lang-bar .call{font-family:"Ubuntu",sans-serif;font-size:13px;color:var(--navy);white-space:nowrap}
.lang-bar .call b{font-weight:400;font-size:17px;margin-left:4px}
.brand{left:35px;top:42px;font-family:"Ubuntu",sans-serif;font-size:26px;color:var(--teal-soft);display:flex;align-items:center;gap:7px;white-space:nowrap}
.brand i{display:block;width:12px;height:12px;border-radius:50%;background:var(--teal-soft)}
.main-nav span{position:absolute;top:72px;display:flex;align-items:center;gap:6px;font-size:10.5px;font-weight:700;color:var(--navy);white-space:nowrap}
.main-nav span::after{content:"";border-left:5px solid var(--teal-soft);border-top:5px solid transparent;border-bottom:5px solid transparent}
.hero{left:21px;top:105px;width:814px;height:281px;background:linear-gradient(90deg,#49b2ae,#7fcdc9);border:1px solid var(--teal);border-radius:3px;box-shadow:0 4px 6px rgba(0,0,0,.15)}
.hero-photo{left:16px;top:15px;width:550px;height:249px;border:4px solid var(--white);border-radius:4px;background:linear-gradient(120deg,#7ab7d6,#e9c8b3 45%,#b7d6e6)}
.dots{left:505px;top:241px;display:flex;gap:4px}
.dots i{width:9px;height:9px;border-radius:50%;background:var(--white)}
.hero-copy{left:590px;top:30px;width:205px;color:var(--white)}
.hero-copy h1{font-family:"Ubuntu",sans-serif;font-weight:400;font-size:24px;line-height:1.15;white-space:nowrap}
.hero-copy h2{font-family:"Ubuntu",sans-serif;font-weight:300;font-size:19px;margin-bottom:8px;white-space:nowrap}
.hero-copy p{font-size:9px;line-height:15px;margin-bottom:6px;color:#eefafa}
.btn-more{display:inline-block;margin-top:4px;background:var(--white);color:var(--navy);border-radius:14px;padding:5px 11px;font-family:"Ubuntu",sans-serif;font-size:12px}
.welcome{left:26px;top:428px;width:520px}
.welcome h3,.box h3{font-family:"Ubuntu",sans-serif;font-weight:400;font-size:16px;color:var(--teal-dark);white-space:nowrap}
.box h3{color:var(--navy)}
.welcome p{font-size:9.1px;line-height:15px;margin-top:10px}
.divider{left:21px;top:637px;width:526px;height:1px;background:#dcdcdc}
.box{border:1px solid var(--line);border-radius:4px;background:var(--white)}
.side-box h3{background:#eaf6f6;padding:9px 14px;height:34px}
.video{left:580px;top:470px;width:248px;height:160px;background:#000;border-radius:4px}
.play{left:102px;top:57px;width:41px;height:41px;border-radius:50%;background:#2e2e2e}
.play::after{content:"";position:absolute;left:16px;top:13px;border-left:12px solid var(--white);border-top:7.5px solid transparent;border-bottom:7.5px solid transparent}
.scrub{left:8px;top:142px;width:232px;height:1px;background:var(--white)}
.scrub i{position:absolute;left:9px;top:-4px;width:9px;height:9px;border-radius:50%;background:var(--white)}
.field{position:absolute;left:12px;width:242px;height:23px;background:var(--field);border-radius:3px;font-size:10px;color:#6a8a8a;padding:5px 9px;white-space:nowrap}
.submit{position:absolute;left:20px;top:258px;background:var(--orange);color:var(--white);font-family:"Ubuntu",sans-serif;font-size:12px;padding:4px 10px;border-radius:3px}
.program-photo{left:14px;top:37px;width:235px;height:94px;border:1px solid var(--teal-soft);border-radius:3px;background:linear-gradient(90deg,#b9c6cc,#8ea7b3 45%,#d8c2b0)}
.program-lead{left:14px;top:145px;width:235px;font-family:"Ubuntu",sans-serif;font-size:11.2px;line-height:15px;color:var(--teal-dark)}
.program-text{left:14px;top:196px;width:235px;font-size:9.1px;line-height:15px}
.course-list{left:12px;top:50px;width:235px;list-style:none}
.course-list li{position:relative;padding:0 0 5px 27px;margin-bottom:7px;border-bottom:1px solid #e6f1f1;font-family:"Ubuntu",sans-serif;font-size:10.3px;line-height:15px;color:var(--teal-dark)}
.course-list li:last-child{border:none}
.course-list li::before{content:"";position:absolute;left:1px;top:1px;width:14px;height:14px;border-radius:50%;background:#dbeeee}
.course-list li::after{content:"";position:absolute;left:7px;top:5px;border-left:5px solid var(--teal);border-top:3.5px solid transparent;border-bottom:3.5px solid transparent}
.footer{left:0;top:966px;width:859px;height:234px;background:linear-gradient(#c6e8e8,#e4f4f4);border-top:1px solid var(--teal)}
.foot-col{position:absolute;top:27px;font-size:9px;font-weight:600;color:var(--navy)}
.foot-col span{display:block;height:22px;padding-top:3px;border-bottom:1px solid #b8dada;white-space:nowrap}
.foot-col span:last-child{border:none}
.foot-brand{left:678px;top:22px;font-family:"Ubuntu",sans-serif;font-size:26px;color:#9ed4d3;display:flex;align-items:center;gap:7px;white-space:nowrap}
.foot-brand i{display:block;width:12px;height:12px;border-radius:50%;background:#9ed4d3}
.foot-line{left:11px;top:184px;width:837px;height:1px;background:var(--teal)}
.copy{left:12px;top:197px;font-size:9.5px;color:var(--navy);white-space:nowrap}
.legal{right:37px;top:197px;font-size:9.5px;color:var(--navy);white-space:nowrap}
</style>
</head>
<body>
<div class="abs hero-band"></div>
<div class="abs top-line"></div>

<header>
  <div class="abs lang-bar">Select Language
    <span class="flags">
      <svg width="26" height="15" viewBox="0 0 26 15"><rect width="26" height="15" fill="#1f3d8a"/><path d="M0 0L26 15M26 0L0 15" stroke="#fff" stroke-width="3"/><path d="M13 0V15M0 7.5H26" stroke="#fff" stroke-width="5"/><path d="M13 0V15M0 7.5H26" stroke="#d21f2b" stroke-width="3"/></svg>
      <svg width="26" height="15" viewBox="0 0 26 15"><rect width="9" height="15" fill="#1f3d8a"/><rect x="9" width="8" height="15" fill="#fff"/><rect x="17" width="9" height="15" fill="#e01b24"/></svg>
      <svg width="26" height="15" viewBox="0 0 26 15"><rect width="26" height="5" fill="#000"/><rect y="5" width="26" height="5" fill="#dd0000"/><rect y="10" width="26" height="5" fill="#ffce00"/></svg>
    </span>
    <span class="call">Call Us <b>+47 53169027</b></span>
  </div>
  <div class="abs brand"><i></i>Mivo Lark</div>
  <nav class="main-nav">
    <span style="left:349px">HOME</span>
    <span style="left:421px">COURSES</span>
    <span style="left:507px">LECTURER</span>
    <span style="left:598px">CONTACT US</span>
    <span style="left:702px">NORWEGIAN/ENGLISH</span>
  </nav>
</header>

<section class="abs hero">
  <div class="abs hero-photo" role="img" aria-label="Rotating banner photo of a dental training session"></div>
  <div class="abs dots"><i></i><i></i><i></i><i></i></div>
  <div class="abs hero-copy">
    <h1>Training on</h1>
    <h2>Endodontic &amp; Dentistry</h2>
    <p>Brantwell Webworks is a web service company, offering a wide range of services which range from designing and development, that is covering almost all the fields in the best possible way.</p>
    <p>To be the best we know what and how to present beautifully the working of the client’s need and their advantages be highlighted.</p>
    <span class="btn-more">learn more</span>
  </div>
</section>

<section class="abs welcome">
  <h3>Welcome to Mivo Lark Website Mainpage</h3>
  <p>Brantwell Webworks is a web service company, offering a wide range of services which range from designing and development, that is covering almost all the fields in the best possible way. To be the best we know what and how to present beautifully the working of the client’s need and their advantages be highlighted. We act in accordance with the Industry certified processes to deliver the best to our clients all over the world.</p>
  <p>Thus, Wanna get ahead in the competition with other websites…. Brantwell Webworks provide you with an attractive and most convincing website to enhance your marketing goals.The only way to success is through the right path and that’s what we provide you. None of the other companies has the result we do. So stick to the best that’s how you will be the best don’t opt for the second best. Our expertise does not limit itself to web development but also it includes Web Hosting, Search Engine Optimization, E-Commerce. We partner hundreds of organization to enhance their business, marketing and profit goals.</p>
</section>
<div class="abs divider"></div>

<aside class="abs box side-box" style="left:566px;top:428px;width:275px;height:214px">
  <h3>Latest Video</h3>
</aside>
<div class="abs video"><div class="abs play"></div><div class="abs scrub"><i></i></div></div>

<aside class="abs box side-box" style="left:566px;top:649px;width:275px;height:299px">
  <h3>Quick Contact Form</h3>
  <div class="field" style="top:46px">type your full name</div>
  <div class="field" style="top:83px;left:14px">type your full name</div>
  <div class="field" style="top:122px;left:16px">type your full name</div>
  <div class="field" style="top:160px;left:16px;height:88px">message</div>
  <span class="submit">Submit</span>
</aside>

<section class="abs box" style="left:17px;top:654px;width:260px;height:300px">
  <h3 class="abs" style="left:14px;top:10px">Our Learning Programs</h3>
  <div class="abs program-photo" role="img" aria-label="Photo of dentists in a hands-on training class"></div>
  <p class="abs program-lead">Brantwell Webworks is a professional website design company dedicated to provide excellent services.</p>
  <p class="abs program-text">We specialized in handling advanced web projects and the ongoing projects that require permanent maintenance and support .We like challenges and do complete these challenge with expertise we like solving questions that arises in such projects</p>
</section>

<section class="abs box" style="left:291px;top:654px;width:259px;height:300px">
  <h3 class="abs" style="left:15px;top:10px">List of Our Dental Courses</h3>
  <ul class="abs course-list">
    <li>The Art of Endodontics Two day Hands-On Laboratory</li>
    <li>Molars Only Alumni Course</li>
    <li>Fast track One Day Hands- Program</li>
    <li>Endos Only a Course Devoted to Endodontic and Implant Surgery</li>
    <li>The Art of Endodontics Two day Hands-On Laboratory</li>
    <li>Molars Only Alumni Course</li>
    <li>Fast track One Day Hands- Program</li>
  </ul>
</section>

<footer class="abs footer">
  <div class="foot-col" style="left:21px;width:92px"><span>Home</span><span>About Us</span><span>Our Courses</span><span>Videos</span><span>Lecturere</span></div>
  <div class="foot-col" style="left:113px;width:118px"><span>Testimonials</span><span>Contact Form</span><span>Learning Programs</span><span>Courses Category</span></div>
  <div class="foot-col" style="left:231px;width:85px"><span>Apply now</span><span>Enquiry</span><span>FAQ</span><span>Contact</span></div>
  <div class="foot-col" style="left:316px;width:138px"><span>Mivo Lark AS</span><span>Endodontic Teaching Center</span><span>Tollbeks vei 41C</span><span>0397 Oslo</span><span>Norway</span></div>
  <div class="foot-col" style="left:461px;top:22px;width:138px"><span>Mivo Lark AS</span><span>Endodontic Teaching Center</span><span>Tollbeks vei 41C</span><span>0397 Oslo</span><span>Norway</span></div>
  <div class="abs foot-brand"><i></i>Mivo Lark</div>
  <div class="abs foot-line"></div>
  <div class="abs copy">© 2012 Company Name &nbsp;|&nbsp; All right reserved</div>
  <div class="abs legal">Terms &amp; Condition &nbsp;&nbsp;|&nbsp;&nbsp; Privacy Policy</div>
</footer>
</body>
</html>
```